Oakhaven Chiropractic 20th Birthday Party

We are a holistic health practice focussing on women's children's health and we need a poster and an invitation to our 20th birthday celebration.

On Sat Nov 24th 12-3pm at OCC

```html
<!DOCTYPE html>
<html lang="en">
<head>
<meta charset="utf-8">
<title>Oakhaven Chiropractic 20th Birthday Celebration</title>
<link href="https://fonts.googleapis.com/css2?family=Questrial&display=swap" rel="stylesheet">
<style>
  :root {
    --teal: #5cb9b7;
    --ink: #3b3b3d;
    --paper: #f4f4f6;
    --white: #ffffff;
  }
  html, body {
    margin: 0;
    padding: 0;
    overflow: hidden;
    background: var(--paper);
  }
  .poster {
    position: relative;
    width: 867px;
    height: 1200px;
    overflow: hidden;
    background: var(--paper);
    font-family: "Questrial", "Century Gothic", sans-serif;
  }
  .poster__shapes {
    position: absolute;
    inset: 0;
  }
  .headline {
    position: absolute;
    left: 430px;
    width: 410px;
    text-align: center;
    color: var(--teal);
    line-height: 1;
  }
  .headline__number {
    top: 505px;
    font-size: 300px;
    letter-spacing: -6px;
  }
  .headline__number sup {
    font-size: 72px;
    vertical-align: top;
    position: relative;
    top: 38px;
    letter-spacing: 0;
    margin-left: 6px;
  }
  .headline__birthday {
    top: 758px;
    font-size: 88px;
    letter-spacing: -3px;
  }
  .headline__celebration {
    top: 842px;
    font-size: 37px;
    letter-spacing: 3px;
    color: var(--ink);
  }
  .event-details {
    position: absolute;
    left: 470px;
    width: 356px;
    top: 948px;
    margin: 0;
    text-align: center;
    color: var(--ink);
    font-size: 36px;
    line-height: 48px;
    letter-spacing: -0.5px;
  }
  .event-details sup {
    font-size: 19px;
    vertical-align: top;
    position: relative;
    top: -4px;
  }
  .brand {
    position: absolute;
    left: 40px;
    width: 346px;
    top: 900px;
    text-align: center;
    color: var(--white);
  }
  .brand__dot {
    width: 64px;
    height: 64px;
    border-radius: 50%;
    background: var(--white);
    margin: 0 auto 18px;
  }
  .brand__name {
    margin: 0;
    font-size: 52px;
    line-height: 58px;
  }
</style>
</head>
<body>
<main class="poster">
  <svg class="poster__shapes" width="867" height="1200" viewBox="0 0 867 1200">
    <defs>
      <linearGradient id="photo-tones" x1="0" y1="0" x2="1" y2="1">
        <stop offset="0" stop-color="#e9ecee"/>
        <stop offset="0.45" stop-color="#d8d3cf"/>
        <stop offset="0.75" stop-color="#cfd6d4"/>
        <stop offset="1" stop-color="#8fb59a"/>
      </linearGradient>
    </defs>
    <polygon class="photo-area" role="img"
             aria-label="Photo of a mother and her toddler playing by a bright window"
             points="0,0 867,0 867,168 0,850" fill="url(#photo-tones)"/>
    <polygon class="teal-corner" points="0,850 213,689 593,1200 0,1200" fill="var(--teal)"/>
  </svg>

  <div class="headline headline__number">20<sup>th</sup></div>
  <div class="headline headline__birthday">BIRTHDAY</div>
  <div class="headline headline__celebration">CELEBRATION</div>

  <p class="event-details">
    On Saturday<br>
    Nov 24<sup>th</sup> 12-3pm<br>
    at OCC
  </p>

  <div class="brand">
    <div class="brand__dot"></div>
    <p class="brand__name">Oakhaven<br>Chiropractic</p>
  </div>
</main>
</body>
</html>
```